Weightloss company needs Business Card

We want a business card that is clean and professional, yet portrays that we are a friendly, innovative, and versatile program designed to fit the needs of our clients.
I would like there to be 2 sides, one side having an appointment card, and the other side containing the logo and business information. There can be decorations on both sides. The logo is attached.

Target Market(s)

Men and women 40-60

Industry/Entity Type

Business

Contact Information for Business Card

Font styles to use
Sans Serif

Requirements
Must have
• The logo, space for business information
Nice to have
• The colors in the logo
Should not have
• No pictures of people or food

```html
<!DOCTYPE html>
<html lang="en">
<head>
<meta charset="utf-8">
<title>Risewell Weightloss – Business Card</title>
<link rel="stylesheet" href="https://fonts.googleapis.com/css2?family=Ubuntu:ital,wght@0,400;0,500;0,700;1,400&display=swap">
<style>
  :root {
    --bg: #bdbec1;
    --paper: #ffffff;
    --red: #e30613;
    --red-deep: #b50d12;
    --ink-grey: #6d6e71;
    --line-grey: #8a8b8e;
    --faint-pink: #f6d3d6;
  }
  * { margin: 0; padding: 0; box-sizing: border-box; }
  html, body {
    width: 1200px; height: 1200px; overflow: hidden;
    background: var(--bg);
    font-family: "Ubuntu", sans-serif;
  }
  .sheet {
    width: 1200px; height: 1200px;
    display: flex; flex-direction: column;
    align-items: center; justify-content: center; gap: 60px;
  }
  .card {
    position: relative;
    width: 840px; height: 480px;
    background: var(--paper);
    overflow: hidden;
    box-shadow: 0 6px 18px rgba(0,0,0,0.18);
  }
  .card__band {
    position: absolute; inset: 0;
    width: 100%; height: 100%;
  }

  /* appointment side */
  .appt-rows {
    position: absolute; left: 60px; top: 50px;
    display: flex; flex-direction: column; gap: 22px;
  }
  .appt-row {
    display: flex; align-items: flex-end; gap: 8px;
    font-style: italic; font-size: 20px; color: var(--line-grey);
  }
  .appt-row__label { width: 56px; }
  .appt-row__line {
    width: 340px; border-bottom: 1.5px solid var(--line-grey);
    margin-bottom: 4px;
  }
  .appt-wordmark {
    position: absolute; left: 390px; top: 150px;
    font-weight: 700; font-size: 54px; line-height: 1;
    color: var(--faint-pink);
  }
  .appt-caption {
    position: absolute; right: 40px; bottom: 34px;
    font-weight: 500; font-size: 26px; letter-spacing: 0.32em;
    color: var(--paper);
  }

  /* info side */
  .holder {
    position: absolute; left: 56px; top: 40px;
  }
  .holder__name {
    font-weight: 700; font-size: 36px; color: var(--red);
    letter-spacing: 0.01em;
  }
  .holder__role { font-size: 24px; color: var(--ink-grey); margin-top: 2px; }
  .contact {
    position: absolute; left: 56px; bottom: 44px;
    font-size: 24px; color: var(--ink-grey); line-height: 1.32;
  }
  .contact__key { color: var(--red); font-weight: 500; }
  .contact__web { margin-top: 10px; }
  .brand {
    position: absolute; right: 400px; top: 195px;
    text-align: right;
    font-weight: 700; font-size: 42px; line-height: 1.12;
    color: var(--red);
  }
  .address {
    position: absolute; right: 44px; bottom: 40px;
    text-align: right; font-size: 24px; line-height: 1.3;
    color: var(--paper);
  }
</style>
</head>
<body>
<main class="sheet">

  <section class="card card--appointments" aria-label="Appointment side">
    <svg class="card__band" viewBox="0 0 840 480" aria-hidden="true">
      <defs>
        <linearGradient id="bandBack" x1="0" y1="0" x2="0" y2="1">
          <stop offset="0" stop-color="var(--red)"/>
          <stop offset="1" stop-color="var(--red-deep)"/>
        </linearGradient>
      </defs>
      <polygon points="340,480 840,480 840,150 640,205 610,238 520,265" fill="url(#bandBack)"/>
    </svg>
    <div class="appt-wordmark">Risewell<br>Weightloss</div>
    <div class="appt-rows">
      <div class="appt-row"><span class="appt-row__label">Date.</span><span class="appt-row__line"></span></div>
      <div class="appt-row"><span class="appt-row__label">Time.</span><span class="appt-row__line"></span></div>
      <div class="appt-row"><span class="appt-row__label">Date.</span><span class="appt-row__line"></span></div>
      <div class="appt-row"><span class="appt-row__label">Time.</span><span class="appt-row__line"></span></div>
      <div class="appt-row"><span class="appt-row__label">Date.</span><span class="appt-row__line"></span></div>
      <div class="appt-row"><span class="appt-row__label">Time.</span><span class="appt-row__line"></span></div>
    </div>
    <div class="appt-caption">appointments</div>
  </section>

  <section class="card card--info" aria-label="Business information side">
    <svg class="card__band" viewBox="0 0 840 480" aria-hidden="true">
      <defs>
        <linearGradient id="bandFront" x1="0" y1="0" x2="0" y2="1">
          <stop offset="0" stop-color="var(--red)"/>
          <stop offset="1" stop-color="var(--red-deep)"/>
        </linearGradient>
      </defs>
      <polygon points="600,0 840,0 840,480 380,480" fill="url(#bandFront)"/>
      <circle cx="560" cy="262" r="82" fill="var(--paper)"/>
    </svg>
    <div class="holder">
      <div class="holder__name">JOHN DOE</div>
      <div class="holder__role">Director</div>
    </div>
    <div class="brand">Risewell<br>Weightloss</div>
    <div class="contact">
      <div><span class="contact__key">T.</span> 111.222.3333</div>
      <div><span class="contact__key">F.</span> 111.222.3333</div>
      <div class="contact__web">www.risewell.com</div>
      <div>info@risewell.com</div>
    </div>
    <div class="address">Dummy City<br>Dummy Country Land</div>
  </section>

</main>
</body>
</html>
```